Upstart Retirement Planning Firm needs help with business card design

Harborview Nest Advisors, LLC is looking for help with business card design. We give advice on investments, insurance, and other financial matters related to retirement. There are some required disclosures that we will provide but mostly we are looking for a professional, classy business card that reflects the theme we have chosen. We have a logo that is attached but we would like to add a phrase; "Turning Your Earned Income Into Retirement Income"

Doubled sided only so that we can add the required disclosures (needed for our industry) on the back of the card. We will provide the exact words for this in 1-2 days.

Target Market(s)

Retirees and Pre-retirees. Professionals 50+ years old

Industry/Entity Type

Financial Planning

Contact Information for Business Card

We currently have two people who will need separate cards so we'd like to have a template so that we can add names for new cards in the future.

For the first run, please show the following information.

Gregor Pelham, MBA, ChFC®, CLU®
Financial Advisor, Registered Representative
gpelham@harborviewnest.example
Phone: (555) 318-2946
Toll Free Fax: (800) 555-0193

Address is
2187 Meadowlark Ridge Rd.
Suite K418
Virginia Beach, VA 23999

Colors
3277b5

Requirements
Must have
• Logo, contact info, small phase to describe business (in description), required legal disclosures on back of the card as follows (in small font)
• Gregor Pelham is a registered representative of and offers securities through Brightmoor Capital Brokerage Corporation, Member FNQX. Brightmoor Capital Brokerage Corporation is a member of the Brightmoor Capital Alliance which is the marketing name for Brightmoor Holding Corporation and its affiliates.
Nice to have
• Rounded edges, raised letters
Should not have
• any colors that aren't in the logo (other than black for font)

```html
<!DOCTYPE html>
<html lang="en">
<head>
<meta charset="utf-8">
<title>Harborview Nest Advisors – Business Card</title>
<link rel="stylesheet" href="https://fonts.googleapis.com/css2?family=Tinos:wght@400;700&display=swap">
<style>
  :root {
    --backdrop: #3b3430;
    --card-black: #1b1b1d;
    --card-black-edge: #262628;
    --brand-blue: #3277b5;
    --deep-blue: #1f5fa8;
    --silver: #b9bcc1;
    --soft-white: #e9e9ea;
    --muted-grey: #3a3a3d;
    --line-dark: #0d0d0e;
  }
  * { box-sizing: border-box; margin: 0; padding: 0; }
  html, body {
    width: 1200px; height: 716px; overflow: hidden;
    background: var(--backdrop);
    font-family: "Tinos", "Times New Roman", serif;
  }
  .stage { position: relative; width: 1200px; height: 716px; }
  .card {
    position: absolute; top: 215px;
    width: 500px; height: 286px;
    border-radius: 10px;
    background: linear-gradient(160deg, var(--card-black-edge), var(--card-black));
    overflow: hidden;
    box-shadow: 0 10px 30px rgba(0,0,0,.45);
  }
  .card--back { left: 70px; }
  .card--front { left: 630px; }

  .back-mark {
    position: absolute; inset: 0;
    display: flex; align-items: center; justify-content: center;
  }
  .back-mark__name {
    color: var(--muted-grey);
    font-size: 30px; letter-spacing: 1px;
    text-align: center; line-height: 1.15;
  }

  .swoosh { position: absolute; inset: 0; width: 500px; height: 286px; }

  .person { position: absolute; left: 22px; top: 34px; }
  .person__name { color: var(--brand-blue); font-size: 20px; font-weight: 400; }
  .person__creds, .person__role { color: var(--soft-white); font-size: 10px; margin-top: 3px; }

  .contact { position: absolute; left: 22px; top: 120px; list-style: none; }
  .contact__item {
    display: flex; align-items: center; gap: 7px;
    color: var(--soft-white); font-size: 12px; line-height: 18px;
  }
  .contact__icon { width: 12px; height: 12px; flex: none; }
  .address { position: absolute; left: 22px; top: 180px; color: var(--soft-white); font-size: 12px; line-height: 16px; font-style: normal; }

  .website { position: absolute; right: 14px; top: 110px; color: var(--soft-white); font-size: 11px; }

  .brand-name {
    position: absolute; right: 70px; bottom: 18px;
    color: var(--soft-white); font-size: 16px; letter-spacing: .5px;
    text-align: center; line-height: 1.2;
  }
</style>
</head>
<body>
<main class="stage">

  <section class="card card--back" aria-label="Card back">
    <div class="back-mark">
      <p class="back-mark__name">Harborview Nest<br>Advisors, LLC</p>
    </div>
  </section>

  <section class="card card--front" aria-label="Card front">
    <svg class="swoosh" viewBox="0 0 500 286" aria-hidden="true">
      <path d="M145 0 C235 10 280 55 325 115 C375 180 440 222 500 232 L500 0 Z" fill="var(--deep-blue)"/>
      <path d="M120 0 C210 10 255 55 300 115 C350 180 420 225 500 240" fill="none" stroke="var(--silver)" stroke-width="6"/>
      <path d="M132 0 C222 10 267 55 312 115 C362 180 430 224 500 236" fill="none" stroke="var(--line-dark)" stroke-width="3"/>
    </svg>

    <div class="person">
      <h1 class="person__name">Gregor Pelham</h1>
      <p class="person__creds">MBA, ChFC®, CLU®</p>
      <p class="person__role">Financial Advisor, Registered Representative</p>
    </div>

    <ul class="contact">
      <li class="contact__item">
        <svg class="contact__icon" viewBox="0 0 12 12"><circle cx="6" cy="6" r="6" fill="var(--brand-blue)"/><path d="M4 3 L5 3 L5.6 4.6 L5 5.2 Q5.6 6.6 6.8 7 L7.4 6.4 L9 7 L9 8 Q6 8.5 4 5 Z" fill="#fff"/></svg>
        (555) 318-2946
      </li>
      <li class="contact__item">
        <svg class="contact__icon" viewBox="0 0 12 12"><circle cx="6" cy="6" r="6" fill="var(--brand-blue)"/><rect x="3" y="4.5" width="6" height="4" fill="#fff"/><rect x="4" y="3" width="4" height="1.5" fill="#fff"/></svg>
        (800) 555-0193
      </li>
      <li class="contact__item">
        <svg class="contact__icon" viewBox="0 0 12 12"><circle cx="6" cy="6" r="6" fill="var(--brand-blue)"/><rect x="3" y="4" width="6" height="4" fill="#fff"/><path d="M3 4 L6 6.3 L9 4" fill="none" stroke="var(--brand-blue)" stroke-width=".8"/></svg>
        gpelham@harborviewnest.example
      </li>
    </ul>

    <address class="address">
      2187 Meadowlark Ridge Rd. Suite<br>
      K418 Virginia Beach, VA 23999
    </address>

    <p class="website">www.harborviewnest.example</p>

    <p class="brand-name">Harborview Nest<br>Advisors, LLC</p>
  </section>

</main>
</body>
</html>
```